Business Cards for IT Consulting Company (Managed Service Provider)

I am looking to have some business cards printed and would like some designs. We are an IT Consulting company based in Vancouver BC. I would like a nice clean and modern look to the cards. I have uploaded all the versions of my logo so parts can be used as needed. Here is a snippit from our website homepage:

Quillbrook Networks Ltd. is an IT Solutions Partner located in Vancouver BC, Canada. We offer IT solutions and support to customers in the greater Vancouver Area. With expertise in Microsoft platforms, as well as Linux and Mac OSX and over 12 years experience in the IT industry, Quillbrook Networks is dedicated to offering our clients top quality service and products. We take pride in the solutions we offer our customers. The greatest compliment a client can give us is to recommend our services.

Quillbrook Networks Ltd. offers a wide range of IT services from onsite service to remote support and managed service solutions. This allows clients to choose the support path that best suits their company’s needs. Supporting many different sized companies from small to enterprise level over the past 12 years Quillbrook Networks has the experience and expertise needed to ensure things run smoothly. Allowing our clients to focus on doing business.

Revolutionizing the way IT services are delivered.

Quillbrook Networks is dedicated to providing our clients with IT solutions that work and grow with them for years to come. This philosophy helps save money in the long run instead of replacing equipment constantly. Far too often IT solutions are not well thought out and while possibly solving the problem at hand, require replacement due to growth or quality within a very short time frame. Quillbrook Networks takes pride in providing solutions that will last and be able to accommodate growth without the need for replacement.

Industry/Entity Type

Information Technology

Contact Information for Business Card

Quillbrook Networks Ltd.
(Employee Name)
Eml: (Employees Email Address)
Web: quillbrook.me
Ph: 604-555-0148

Font styles to use
Serif
Sans Serif

Requirements
Must have
• The Company logo and company colors.
Nice to have
• - Our tag line: "Revolutionizing IT Services" or "Revolutionizing the way IT services are delivered."
• - Also I really like the idea of nature and technology together blending which is sort of where my logo came from so integrating that somehow onto the business cards would be great.

```html
<!DOCTYPE html>
<html lang="en">
<head>
<meta charset="utf-8">
<title>Quillbrook Networks Ltd. – Business Cards</title>
<link href="https://fonts.googleapis.com/css2?family=Montserrat:wght@500&family=Roboto:ital,wght@0,400;0,500;1,400&display=swap" rel="stylesheet">
<style>
  :root {
    --backdrop: #a9a7a8;
    --card: #1c1c1e;
    --brand-blue: #1b8fd6;
    --band-grey: #5a595c;
    --text-light: #e6e6e6;
    --text-muted: #c9c9c9;
  }
  html, body {
    margin: 0;
    width: 1200px;
    height: 1200px;
    overflow: hidden;
    background: var(--backdrop);
  }
  .canvas { position: relative; width: 1200px; height: 1200px; }
  .card {
    position: absolute;
    width: 713px;
    height: 418px;
    background: var(--card);
    overflow: hidden;
    font-family: "Roboto", Arial, sans-serif;
  }
  .card--front { left: 238px; top: 118px; }
  .card--back  { left: 231px; top: 644px; }

  .wordmark {
    position: absolute;
    font-family: "Montserrat", Arial, sans-serif;
    font-weight: 500;
    color: var(--brand-blue);
    white-space: nowrap;
    margin: 0;
  }
  .card--front .wordmark {
    left: 0; right: 0; top: 168px;
    text-align: center;
    font-size: 40px;
  }
  .card--back .wordmark {
    left: 300px; top: 68px;
    font-size: 30px;
  }

  .tagline-row {
    position: absolute;
    left: 0; right: 0; top: 376px;
    display: flex;
    align-items: center;
    justify-content: center;
    gap: 16px;
  }
  .tagline-rule { width: 110px; height: 2px; background: var(--brand-blue); }
  .tagline { color: var(--text-light); font-size: 19px; letter-spacing: 0.2px; }

  .person { position: absolute; left: 39px; top: 68px; }
  .person__name { margin: 0; color: var(--brand-blue); font-weight: 500; font-size: 26px; }
  .person__title { margin: 6px 0 0; color: var(--text-muted); font-style: italic; font-size: 17px; }

  .contact-list {
    position: absolute; left: 38px; top: 231px;
    list-style: none; margin: 0; padding: 0;
  }
  .contact-list li {
    display: flex; align-items: center; gap: 16px;
    height: 27.5px;
    color: var(--text-light); font-size: 18px;
  }
  .contact-list svg { width: 19px; height: 16px; fill: var(--text-muted); }

  .wave { position: absolute; left: 0; top: 0; }
  .wave__grey { fill: var(--band-grey); }
  .wave__gap  { fill: var(--card); }
  .wave__blue { fill: var(--brand-blue); }

  .wave-tagline {
    position: absolute; right: 31px; top: 335px;
    margin: 0; text-align: right;
    color: #ffffff; font-size: 18px; line-height: 25px;
  }
</style>
</head>
<body>
<main class="canvas">

  <section class="card card--front" aria-label="Business card front">
    <p class="wordmark">Quillbrook Networks Ltd.</p>
    <div class="tagline-row">
      <span class="tagline-rule"></span>
      <span class="tagline">Revolutionizing IT Services</span>
      <span class="tagline-rule"></span>
    </div>
  </section>

  <section class="card card--back" aria-label="Business card back">
    <div class="person">
      <h1 class="person__name">Daniel Reyes</h1>
      <p class="person__title">Managing Director</p>
    </div>

    <p class="wordmark">Quillbrook Networks Ltd.</p>

    <ul class="contact-list">
      <li>
        <svg viewBox="0 0 20 16" aria-hidden="true"><path d="M1 5c0-3 4-4 9-4s9 1 9 4l-1 2-4-1V4H6v2L2 7z"/><path d="M4 8h12l2 7H2z"/><circle cx="10" cy="11.5" r="2" fill="#1c1c1e"/></svg>
        <span>604-555-0148</span>
      </li>
      <li>
        <svg viewBox="0 0 20 16" aria-hidden="true"><circle cx="10" cy="8" r="7"/><path d="M3 8h14M10 1v14M5 4h10M5 12h10" stroke="#1c1c1e" stroke-width="1.2" fill="none"/><ellipse cx="10" cy="8" rx="3" ry="7" stroke="#1c1c1e" stroke-width="1.2" fill="none"/></svg>
        <span>www.quillbrook.me</span>
      </li>
      <li>
        <svg viewBox="0 0 20 16" aria-hidden="true"><rect x="1" y="2" width="18" height="12"/><path d="M1 2l9 7 9-7M1 14l7-6M19 14l-7-6" stroke="#1c1c1e" stroke-width="1.3" fill="none"/></svg>
        <span>support@quillbrook.me</span>
      </li>
    </ul>

    <svg class="wave" width="713" height="418" viewBox="0 0 713 418" aria-hidden="true">
      <path class="wave__grey" d="M0,330 C170,352 330,385 450,318 C560,255 620,216 713,210 V418 H0 Z"/>
      <path class="wave__gap"  d="M0,350 C170,370 340,392 462,332 C572,278 632,242 713,232 V418 H0 Z"/>
      <path class="wave__blue" d="M0,380 C200,384 380,378 500,328 C592,290 650,244 713,238 V418 H0 Z"/>
    </svg>

    <p class="wave-tagline">Revolutionizing the<br>way IT services are delivered</p>
  </section>

</main>
</body>
</html>
```